Social Media Graphics - Oakline Push REVISED

Create 6-7 individual social media graphics (square size) to encourage folks to join our online course called:

The Harvest Ledger Circle
How to Launch a Multi-Million Business From Scratch
Sign Up Today!

IMPORTANT: Make the largest and most prominent text on the graphic be: How to Launch a Multi-Million Business From Scratch

For the color scheme of the graphics, let's try a blue color palette; make sure the graphics appeal to both men and women

Make sure each graphic contains 1 of the 3 pics attached (crop pic as needed); and make sure one of the graphics is all TEXT only.

Target Market(s)

men and women looking to start a business

Industry/Entity Type

Entrepreneurship

Colors
0054AA
0677BA
7BADD7
CADEEF
E8F1F8

Requirements
Must have
• All the text and use the 3 pics provided; one graphic can be all text; Simple, modern design that's easy to read

```html
<!DOCTYPE html>
<html lang="en">
<head>
<meta charset="utf-8">
<title>The Harvest Ledger Circle – Social Graphic</title>
<link href="https://fonts.googleapis.com/css2?family=Anton&family=Archivo+Black&display=swap" rel="stylesheet">
<style>
  :root {
    --sky: #7aabd6;
    --sky-light: #cadeef;
    --glow: #ffffff;
    --band: #331e1c;
    --accent-red: #b10024;
    --navy: #1e1d3a;
    --white: #ffffff;
  }
  html, body {
    margin: 0;
    padding: 0;
    width: 1200px;
    height: 1200px;
    overflow: hidden;
    background: var(--sky);
  }
  .graphic {
    display: block;
    width: 1200px;
    height: 1200px;
  }
  .course-title {
    font-family: 'Anton', 'Impact', sans-serif;
    fill: var(--white);
    letter-spacing: 2px;
  }
  .headline {
    font-family: 'Anton', 'Impact', sans-serif;
    fill: var(--navy);
  }
  .headline-accent {
    fill: var(--accent-red);
  }
  .rule {
    stroke: var(--navy);
    stroke-width: 4;
  }
  .cta-button {
    fill: var(--navy);
  }
  .cta-label {
    font-family: 'Archivo Black', 'Arial Black', sans-serif;
    fill: var(--white);
    letter-spacing: 4px;
  }
</style>
</head>
<body>
<svg class="graphic" viewBox="0 0 1200 1200" xmlns="http://www.w3.org/2000/svg">
  <defs>
    <radialGradient id="skyGlow" cx="600" cy="110" r="560" gradientUnits="userSpaceOnUse">
      <stop offset="0" stop-color="var(--glow)"/>
      <stop offset="0.35" stop-color="#f2f7fc"/>
      <stop offset="1" stop-color="var(--sky)"/>
    </radialGradient>
    <linearGradient id="hostsTone" x1="0" y1="0" x2="1" y2="0">
      <stop offset="0" stop-color="#e2485f"/>
      <stop offset="0.5" stop-color="#5a3a34"/>
      <stop offset="1" stop-color="#1f1a1a"/>
    </linearGradient>
  </defs>

  <!-- background -->
  <rect class="backdrop" x="0" y="0" width="1200" height="1200" fill="var(--sky)"/>
  <rect class="backdrop-glow" x="0" y="0" width="1200" height="500" fill="url(#skyGlow)"/>

  <!-- course hosts photo -->
  <rect class="hosts-photo" x="355" y="47" width="505" height="450" rx="6"
        fill="url(#hostsTone)" opacity="0.85"
        role="img" aria-label="Photo of the two smiling course hosts, a woman in a red dress with arms crossed and a man in a black shirt and vest"/>

  <!-- course title band -->
  <rect class="band-edge" x="0" y="497" width="1200" height="10" fill="var(--accent-red)"/>
  <rect class="band" x="0" y="507" width="1200" height="108" fill="var(--band)"/>
  <text class="course-title" x="600" y="591" font-size="74" text-anchor="middle">THE HARVEST LEDGER CIRCLE</text>

  <!-- main headline -->
  <text class="headline" x="600" y="740" font-size="112" text-anchor="middle">HOW TO LAUNCH A</text>
  <text class="headline headline-accent" x="105" y="860" font-size="112" textLength="990" lengthAdjust="spacingAndGlyphs">MULTI-MILLION BUSINESS</text>
  <line class="rule" x1="105" y1="935" x2="290" y2="935"/>
  <text class="headline" x="600" y="980" font-size="112" text-anchor="middle">FROM SCRATCH</text>
  <line class="rule" x1="910" y1="935" x2="1095" y2="935"/>

  <!-- call to action -->
  <rect class="cta-button" x="410" y="1040" width="380" height="70" rx="35"/>
  <text class="cta-label" x="600" y="1088" font-size="32" text-anchor="middle">SIGN UP TODAY</text>
</svg>
</body>
</html>
```